E learning Platform for privacy

Current website is as below and its more of a shell.
I need someone to take the text and content and design it properly.
https://study.vornaquill.com/

After that, design has to be implemented with elementor and wordpress
https://elementor.com/

```html
<!DOCTYPE html>
<html lang="en">
<head>
<meta charset="utf-8">
<title>Vornaquill Learning Centre</title>
<link href="https://fonts.googleapis.com/css2?family=Rajdhani:wght@500;600;700&family=IBM+Plex+Sans:wght@400;500;600&family=Open+Sans:wght@400;600;700&display=swap" rel="stylesheet">
<style>
:root{
  --orange:#e8501f;
  --orange-soft:#f47a2c;
  --navy:#1c3765;
  --ink:#1d1d24;
  --grey:#5d5d66;
  --pale:#f3f3f8;
  --footer:#13151c;
  --white:#ffffff;
}
*{box-sizing:border-box;margin:0;padding:0}
html,body{width:1200px;height:5291px;overflow:hidden}
body{font-family:"Open Sans",sans-serif;color:var(--ink);background:var(--white);position:relative}
.abs{position:absolute}
.heading{font-family:"Rajdhani",sans-serif;font-weight:700;color:var(--ink);text-align:center}
.underline{width:58px;height:4px;background:var(--orange);margin:0 auto}

/* top bar + hero */
.topbar{position:absolute;top:0;left:0;width:1200px;height:29px;background:var(--orange);color:#fff;font-size:13px;display:flex;justify-content:flex-end;align-items:center;gap:40px;padding-right:144px;z-index:3}
.topbar span{display:flex;align-items:center;gap:8px}
.hero{position:absolute;top:0;left:0;width:1200px;height:801px;background:linear-gradient(100deg,#f4f3f0 0%,#e9e6e1 35%,#cfc9c2 60%,#8f8780 85%,#5e5751 100%)}
.logo{position:absolute;left:144px;top:66px;color:var(--orange);font-family:"Rajdhani",sans-serif;font-weight:700}
.logo .name{font-size:36px;letter-spacing:3px;line-height:1}
.logo .sub{font-size:9px;letter-spacing:4px;color:#333;margin-top:2px}
.nav{position:absolute;top:84px;left:410px;display:flex;align-items:center;gap:26px;font-size:16px;color:#fff}
.nav .active{color:var(--orange)}
.nav .pill{background:var(--orange);color:#fff;font-size:12px;font-weight:700;padding:10px 18px;border-radius:3px}
.hero-title{position:absolute;left:141px;top:284px;font-family:"Rajdhani",sans-serif;font-size:58px;line-height:58px;font-weight:700;color:#111}
.hero-lead{position:absolute;left:142px;top:418px;font-size:18px;line-height:28px;color:#222;font-family:"IBM Plex Sans",sans-serif}
.hero-actions{position:absolute;left:142px;top:493px;display:flex;gap:12px}
.btn{display:inline-block;font-size:13px;font-weight:700;text-transform:uppercase;padding:13px 34px;border-radius:2px}
.btn-solid{background:var(--orange);color:#fff}
.btn-ghost{background:#fff;color:var(--orange);border:1px solid #ddd}
.dots{position:absolute;left:146px;top:577px;display:flex;gap:10px;align-items:center}
.dots i{width:10px;height:10px;border-radius:50%;background:#111;display:block}
.dots i.on{width:16px;height:16px;border:2px solid #111;background:radial-gradient(#111 40%,transparent 45%)}

/* cards */
.card{position:absolute;width:288px}
.card .photo{height:232px}
.card .body{position:relative;margin:-16px 0 0 20px;background:#fff;border-left:2px solid var(--orange);padding:14px 16px 0 22px}
.card h3{font-family:"Open Sans",sans-serif;font-size:13px;font-weight:700;text-transform:uppercase;line-height:22px;color:#222}
.meta{font-size:12px;color:var(--orange);font-weight:700;margin:8px 0 10px;display:flex;gap:14px}
.card p{font-size:13px;line-height:22px;color:#555}
.readmore{display:inline-block;margin-top:14px;background:var(--orange);color:#fff;font-size:11px;font-weight:700;padding:8px 22px;border-radius:20px}

/* welcome */
.welcome{position:absolute;top:1465px;left:0;width:1200px;height:580px;background:linear-gradient(90deg,#8b8177 0%,#cbbfb2 30%,#6e665f 55%,#3d5a3a 75%,#2e2824 100%)}
.welcome-box{position:absolute;left:144px;top:1572px;width:411px;height:377px;background:#fff;padding:30px 28px;font-family:"IBM Plex Sans",sans-serif}
.welcome-box .small{font-size:26px;line-height:32px;color:#333}
.welcome-box .big{font-family:"Rajdhani",sans-serif;font-size:34px;font-weight:600;color:#222;line-height:40px;white-space:nowrap;letter-spacing:-0.3px}
.welcome-box hr{width:58px;border:0;height:3px;background:#222;margin:18px 0 24px}
.welcome-box p{font-size:14px;line-height:23px;color:#555}
.welcome-box .outline{display:inline-block;margin-top:18px;border:2px solid var(--orange);color:var(--orange);font-size:13px;font-weight:600;padding:6px 16px}

/* stats */
.stats{position:absolute;top:2045px;left:0;width:1200px;height:411px;background:var(--navy)}
.stat{position:absolute;top:111px;width:200px;height:200px;text-align:center;color:#fff}
.stat svg{position:absolute;left:0;top:0}
.stat .num{position:absolute;left:0;width:200px;font-family:"Rajdhani",sans-serif;font-weight:700;font-size:36px;color:var(--orange-soft)}
.stat .lbl{position:absolute;left:0;width:200px;font-size:16px;line-height:18px;font-weight:500}

/* why */
.why{position:absolute;top:2456px;left:0;width:1200px;height:1040px;background:var(--pale)}
.why-card{position:absolute;width:273px;height:300px;background:#fff;box-shadow:0 1px 4px rgba(0,0,0,.12);text-align:center;padding:26px 18px 0}
.why-card .ic{width:88px;height:88px;border-radius:50%;background:var(--orange);margin:0 auto 26px;display:flex;align-items:center;justify-content:center}
.why-card h4{font-size:15px;font-weight:700;text-transform:uppercase;line-height:22px;color:#222}
.why-card p{font-size:13px;line-height:22px;color:#555;margin-top:10px}

/* clients */
.clients{position:absolute;top:4223px;left:0;width:1200px;height:596px;background:linear-gradient(180deg,#f58a2e 0%,#f06a26 50%,#e2471d 100%)}
.quote{position:absolute;top:187px;width:412px;height:193px;background:rgba(255,255,255,.88);padding:22px 24px;font-size:13px;line-height:26px;color:#666}
.person{position:absolute;top:410px;display:flex;gap:14px;align-items:center;color:#fff;font-size:13px;font-weight:600}
.person .av{width:62px;height:62px;border-radius:50%;background:#d8c7b8;border:3px solid #fff}
.stars{color:#ffd34d;letter-spacing:2px}

/* footer */
.footer{position:absolute;top:4819px;left:0;width:1200px;height:472px;background:var(--footer);color:#fff}
.footer h5{font-size:15px;font-weight:700;text-transform:uppercase}
.footer .txt{font-size:13px;line-height:20px;color:#e6e6e6}
.social{width:24px;height:24px;border:1px solid #fff;border-radius:50%;display:block}
.copy{position:absolute;top:429px;width:1200px;text-align:center;font-size:13px;color:#ddd}
</style>
</head>
<body>

<div class="hero" role="img" aria-label="Photo of a woman with glasses working on a laptop in a bright room"></div>
<div class="topbar">
  <span><svg width="14" height="14" viewBox="0 0 24 24"><path fill="#fff" d="M6.6 10.8a15 15 0 006.6 6.6l2.2-2.2c.3-.3.7-.4 1-.2 1.1.4 2.3.6 3.6.6.6 0 1 .4 1 1V20c0 .6-.4 1-1 1A17 17 0 013 4c0-.6.4-1 1-1h3.5c.6 0 1 .4 1 1 0 1.3.2 2.5.6 3.6.1.3 0 .7-.2 1z"/></svg>+1 (800) 555 0142</span>
  <span><svg width="16" height="12" viewBox="0 0 16 12"><rect width="16" height="12" rx="1" fill="#fff"/><path d="M0 1l8 6 8-6" stroke="#e8501f" stroke-width="1.4" fill="none"/></svg>support@study.vornaquill.com</span>
</div>
<div class="logo"><div class="name">VORNAQUILL</div><div class="sub">LEARNING CENTRE</div></div>
<div class="nav">
  <span class="active">Home</span><span>COURSES</span><span>ABOUT US</span><span>BLOGS</span><span>Contact</span>
  <span class="pill">SIGN IN</span><span class="pill" style="margin-left:-14px">REGISTER</span>
</div>
<h1 class="hero-title">Privacy Skills for<br>Professionals</h1>
<p class="hero-lead">Largest online e-learning resource for<br>data protection &amp; privacy</p>
<div class="hero-actions">
  <span class="btn btn-solid">Get Trained</span><span class="btn btn-ghost">Learn More</span>
</div>
<div class="dots"><i class="on"></i><i></i><i></i><i></i></div>
<svg class="abs" style="left:0;top:730px" width="1200" height="75" viewBox="0 0 1200 75">
  <polygon points="0,62 600,12 1200,62 1200,75 0,75" fill="#fff"/>
  <polyline points="0,62 600,12 1200,62" fill="none" stroke="#e8501f" stroke-width="5"/>
</svg>

<!-- featured courses -->
<h2 class="heading abs" style="top:850px;width:1200px;font-size:38px">Featured Courses</h2>
<div class="underline abs" style="top:918px;left:571px"></div>

<div class="card" style="left:144px;top:966px">
  <div class="photo" role="img" aria-label="Photo of smiling students in a classroom" style="background:linear-gradient(135deg,#6c8f4f,#c4a27a 50%,#4f6a7e)"></div>
  <div class="body"><h3>How to scale social impact</h3><div class="meta"><span>▦ Dec 19, 2019</span><span>● Mr. Example</span></div><p>Sed ut perspiciatis unde omnis iste natus error sit voluptatem accntium domque lauda</p><span class="readmore">READ MORE</span></div>
</div>
<div class="card" style="left:456px;top:966px">
  <div class="photo" role="img" aria-label="Photo of hands typing on a laptop with a network graphic" style="background:linear-gradient(135deg,#f1efec,#b9aea5 55%,#5f534d)"></div>
  <div class="body"><h3>Global Social Entrepreneurship</h3><div class="meta"><span>▦ Dec 19, 2019</span><span>● Mr. Example</span></div><p>Sed ut perspiciatis unde omnis iste natus error sit voluptatem accntium domque lauda</p><span class="readmore">READ MORE</span></div>
</div>
<div class="card" style="left:769px;top:966px">
  <div class="photo" role="img" aria-label="Photo of students working at computers in a lab" style="background:linear-gradient(135deg,#9aa3a8,#3d4a52 50%,#7c6d5c)"></div>
  <div class="body"><h3>Open Demonstration Course</h3><div class="meta"><span>▦ Dec 19, 2019</span><span>● Mr. Example</span></div><p>Sed ut perspiciatis unde omnis iste natus error sit voluptatem accntium domque lauda</p><span class="readmore">READ MORE</span></div>
</div>

<!-- welcome -->
<div class="welcome" role="img" aria-label="Photo of adult learners taking notes in a seminar"></div>
<div class="welcome-box">
  <div class="small">Welcome to</div>
  <div class="big">Vornaquill Learning Centre</div>
  <hr>
  <p>Sed ut perspiciatis unde omnis iste natus error sit voluptatem accusantium doloremque laudam, totam rem aperiam, eaque ipsa quae ab illo inveore veritatis et quasi architecto beatae vitae dicta sunt explicabo. Nemo enim ipsavoluptatem quia voluptas sit aspernatur</p>
  <span class="outline">LEARN MORE</span>
</div>

<!-- stats -->
<div class="stats">
  <div class="stat" style="left:251px">
    <svg width="200" height="200"><circle cx="100" cy="100" r="88" fill="none" stroke="#fff" stroke-width="7"/><path d="M100 12 A88 88 0 0 0 40 164" fill="none" stroke="#f47a2c" stroke-width="7"/></svg>
    <svg class="abs" style="left:84px;top:34px" width="32" height="32" viewBox="0 0 24 24"><circle cx="12" cy="12" r="12" fill="#fff"/><circle cx="12" cy="9" r="4" fill="#1c3765"/><path d="M5 19a7 6 0 0114 0" fill="#1c3765"/></svg>
    <div class="num" style="top:74px">6,375</div>
    <div class="lbl" style="top:122px;font-size:14px;font-weight:600">ENROLLED<br>STUDENTS</div>
  </div>
  <div class="stat" style="left:498px">
    <svg width="200" height="200"><circle cx="100" cy="100" r="88" fill="none" stroke="#f47a2c" stroke-width="7"/></svg>
    <svg class="abs" style="left:86px;top:40px" width="28" height="32" viewBox="0 0 20 24"><rect width="20" height="24" rx="2" fill="#fff"/><rect x="4" y="6" width="12" height="2" fill="#1c3765"/><rect x="4" y="11" width="12" height="2" fill="#1c3765"/></svg>
    <div class="num" style="top:82px">114</div>
    <div class="lbl" style="top:134px;font-size:18px">LESSONS</div>
  </div>
  <div class="stat" style="left:749px">
    <svg width="200" height="200"><circle cx="100" cy="100" r="88" fill="none" stroke="#f47a2c" stroke-width="7"/><path d="M100 12 A88 88 0 0 1 188 100" fill="none" stroke="#fff" stroke-width="7"/></svg>
    <svg class="abs" style="left:88px;top:42px" width="26" height="30" viewBox="0 0 20 24"><path d="M0 2a2 2 0 012-2h11l7 7v15a2 2 0 01-2 2H2a2 2 0 01-2-2z" fill="#fff"/><polygon points="7,10 14,14 7,18" fill="#1c3765"/></svg>
    <div class="num" style="top:82px">169</div>
    <div class="lbl" style="top:136px;font-size:18px">VIDEOS</div>
  </div>
</div>

<!-- why -->
<div class="why">
  <h2 class="heading abs" style="top:92px;width:1200px;font-size:36px">Why the (Vornaquill) Learning Centre?</h2>
  <p class="abs" style="top:180px;width:1200px;text-align:center;font-size:13px;line-height:24px;color:#444">Our mission at the Vornaquill Learning Centre is to provide business and job opportunities,<br>as well as to enhance personal and career advancement for data protection / privacy professionals.</p>

  <div class="why-card" style="left:154px;top:283px"><div class="ic"><svg width="46" height="40"><rect x="3" y="3" width="40" height="26" rx="2" fill="none" stroke="#fff" stroke-width="3"/><rect x="15" y="33" width="16" height="4" fill="#fff"/></svg></div><h4>Comprehensive Roadmap</h4><p>Our objective is to provide a comprehensive competency roadmap, instead of one-off courses, whether you are a new or experienced officer</p></div>
  <div class="why-card" style="left:466px;top:283px"><div class="ic"><svg width="46" height="40"><circle cx="23" cy="14" r="10" fill="none" stroke="#fff" stroke-width="3"/><path d="M6 38h34" stroke="#fff" stroke-width="3"/></svg></div><h4>Operational Perspective</h4><p>We cover a broad range of data protection topics from both a legal and operational perspective, covering multiple jurisdictions and drawing from enforcement</p></div>
  <div class="why-card" style="left:779px;top:283px"><div class="ic"><svg width="46" height="40"><rect x="3" y="5" width="36" height="28" rx="2" fill="none" stroke="#fff" stroke-width="3"/><path d="M12 19l6 6 12-12" fill="none" stroke="#fff" stroke-width="3"/></svg></div><h4>Academic &amp; International Certification</h4><p>We partner with prominent universities in the region as well as international certification bodies such as the International</p></div>

  <div class="why-card" style="left:154px;top:620px"><div class="ic"><svg width="46" height="40"><rect x="4" y="4" width="16" height="14" fill="none" stroke="#fff" stroke-width="3"/><rect x="26" y="4" width="16" height="14" fill="none" stroke="#fff" stroke-width="3"/><rect x="15" y="23" width="16" height="14" fill="none" stroke="#fff" stroke-width="3"/></svg></div><h4>Modular Approach<br>&amp; Flexibility</h4><p>All our courses are modular in nature to cater to the busy professional, meaning that you can take the courses separately first</p></div>
  <div class="why-card" style="left:466px;top:620px"><div class="ic"><svg width="46" height="40"><circle cx="9" cy="9" r="5" fill="#fff"/><circle cx="37" cy="9" r="5" fill="#fff"/><circle cx="23" cy="32" r="5" fill="#fff"/><path d="M9 9L37 9L23 32Z" fill="none" stroke="#fff" stroke-width="2"/></svg></div><h4>Network with other peers</h4><p>Participate in our online communities and discussion rooms and your network with other like-minded course participants; share best practices</p></div>
  <div class="why-card" style="left:779px;top:620px"><div class="ic"><svg width="46" height="40"><rect x="4" y="12" width="38" height="24" rx="2" fill="none" stroke="#fff" stroke-width="3"/><path d="M16 12V6h14v6" fill="none" stroke="#fff" stroke-width="3"/></svg></div><h4>Business and Job Opportunities</h4><p>Collaborate with other professionals on potential business opportunities whether it relates to consultancy, legal or training services.</p></div>
</div>
<svg class="abs" style="left:0;top:3492px" width="1200" height="78" viewBox="0 0 1200 78">
  <polygon points="0,0 1200,0 1200,12 600,72 0,12" fill="#e8501f"/>
  <polygon points="0,0 1200,0 1200,4 600,60 0,4" fill="#f3f3f8"/>
</svg>

<!-- latest news -->
<h2 class="heading abs" style="top:3636px;width:1200px;font-size:38px">LATEST NEWS</h2>
<div class="underline abs" style="top:3703px;left:571px"></div>

<div class="card" style="left:144px;top:3757px">
  <div class="photo" role="img" aria-label="Photo of a student reading in a library" style="height:190px;background:linear-gradient(135deg,#7a4a2a,#c88a4c 50%,#4a3a2c)"></div>
  <div class="body"><h3>Sed ut perspiciatis unde omnis iste natus</h3><div class="meta"><span>▦ Feb 3, 2020</span></div><p>Sed ut perspiciatis unde omnis iste natus error sit voluptatem accntium domque laudantium, totam</p></div>
</div>
<div class="card" style="left:456px;top:3757px">
  <div class="photo" role="img" aria-label="Photo of students writing an exam" style="height:190px;background:linear-gradient(135deg,#3f6f94,#b8c5cf 55%,#6c5b4c)"></div>
  <div class="body"><h3>Sed ut perspiciatis unde omnis iste natus</h3><div class="meta"><span>▦ Feb 3, 2020</span></div><p>Sed ut perspiciatis unde omnis iste natus error sit voluptatem accntium domque laudantium, totam</p></div>
</div>
<div class="card" style="left:769px;top:3757px">
  <div class="photo" role="img" aria-label="Photo of a man working on a laptop by a window" style="height:190px;background:linear-gradient(135deg,#d9dccf,#8c8f84 50%,#2f3330)"></div>
  <div class="body"><h3>Sed ut perspiciatis unde omnis iste natus</h3><div class="meta"><span>▦ Feb 3, 2020</span></div><p>Sed ut perspiciatis unde omnis iste natus error sit voluptatem accntium domque laudantium, totam</p></div>
</div>

<!-- clients -->
<div class="clients" role="img" aria-label="Orange toned photo of smiling learners behind the testimonials">
  <h2 class="heading abs" style="top:86px;width:1200px;font-size:36px;color:#fff">OUR CLIENTS SAYS</h2>
  <div class="abs" style="top:138px;left:571px;width:58px;height:4px;background:#fff"></div>
  <div class="quote" style="left:168px"><span style="color:#bbb;font-size:30px;font-weight:700;vertical-align:-10px">“</span> Sed ut perspiciatis unde omnis iste natus error sit voluptatem accusantium doloremque laudantium, totam rem aperiam, eaque ipsa quae ab illo inventore veritatis et quasi architecto beatae vitae dicta suntemo enim ipsam voluptatem quia voluptas sit aspernatur aut odit aut fugit, sed quia consequuntur magni</div>
  <div class="quote" style="left:623px"><span style="color:#bbb;font-size:30px;font-weight:700;vertical-align:-10px">“</span> Sed ut perspiciatis unde omnis iste natus error sit voluptatem accusantium doloremque laudantium, totam rem aperiam, eaque ipsa quae ab illo inventore veritatis et quasi architecto beatae vitae dicta suntemo enim ipsam voluptatem quia voluptas sit aspernatur aut odit aut fugit, sed quia consequuntur magni</div>
  <div class="person" style="left:164px"><div class="av" role="img" aria-label="Client portrait"></div><div>Neque porro quisquam<br>dolorem ipsum<br><span class="stars">★★★★★</span></div></div>
  <div class="person" style="left:620px"><div class="av" role="img" aria-label="Client portrait"></div><div>Neque porro quisquam<br>dolorem ipsum<br><span class="stars">★★★★★</span></div></div>
</div>

<!-- footer -->
<div class="footer">
  <div class="abs" style="left:144px;top:82px;font-family:Rajdhani,sans-serif;font-weight:700;color:#fff">
    <div style="font-size:32px;letter-spacing:3px;line-height:1">VORNAQUILL</div>
    <div style="font-size:8px;letter-spacing:4px;margin-top:2px">LEARNING CENTRE</div>
  </div>
  <div class="abs" style="left:146px;top:150px;display:flex;gap:6px">
    <i class="social"></i><i class="social"></i><i class="social"></i><i class="social"></i>
  </div>

  <div class="abs" style="left:370px;top:78px;width:280px">
    <h5>Sign up for newsletter</h5>
    <p class="txt" style="margin-top:30px">excepteur sint occaecat cupidatat non proident, sunt in culpa qui officia deserunt</p>
    <div style="margin-top:14px;width:272px;height:36px;background:#fff;border-radius:18px;font-size:11px;color:#666;padding:11px 16px">Enter email</div>
    <div style="margin-top:14px;width:138px;height:34px;background:#f47a1c;border-radius:17px;font-size:13px;font-weight:700;text-align:center;line-height:34px">SUBSCRIBE</div>
  </div>

  <div class="abs" style="left:686px;top:80px;width:260px">
    <h5>Contact Us</h5>
    <div class="txt" style="position:relative;margin-top:30px;padding-left:38px"><svg class="abs" style="left:2px;top:4px" width="16" height="22" viewBox="0 0 16 22"><path d="M8 0a8 8 0 018 8c0 6-8 14-8 14S0 14 0 8a8 8 0 018-8z" fill="#fff"/><circle cx="8" cy="8" r="3" fill="#13151c"/></svg>418 Alder Row STE 12<br>418 Alder Row, Brightwater,<br>TX 75390, USA</div>
    <div class="txt" style="position:relative;margin-top:14px;padding-left:38px"><svg class="abs" style="left:0;top:2px" width="18" height="18" viewBox="0 0 24 24"><path fill="#fff" d="M6.6 10.8a15 15 0 006.6 6.6l2.2-2.2c.3-.3.7-.4 1-.2 1.1.4 2.3.6 3.6.6.6 0 1 .4 1 1V20c0 .6-.4 1-1 1A17 17 0 013 4c0-.6.4-1 1-1h3.5c.6 0 1 .4 1 1 0 1.3.2 2.5.6 3.6.1.3 0 .7-.2 1z"/></svg>Phone:<br>+1 (800) 555 0142</div>
    <div class="txt" style="position:relative;margin-top:14px;padding-left:38px"><svg class="abs" style="left:0;top:4px" width="18" height="14" viewBox="0 0 16 12"><rect width="16" height="12" rx="1" fill="#fff"/><path d="M0 1l8 6 8-6" stroke="#13151c" stroke-width="1.4" fill="none"/></svg>Email:<br>support@study.vornaquill.com</div>
  </div>

  <div class="abs" style="left:960px;top:80px">
    <h5>Quick Links</h5>
    <div class="txt" style="margin-top:26px;line-height:27px;padding-left:4px">Home<br>Blogs<br>Courses<br>Contact Us<br>About Us<br>Sign In</div>
  </div>

  <div class="copy">Copyright © Vornaquill Learning Centre 2020. All rights reserved. | Privacy Policy</div>
</div>

</body>
</html>
```